A start-up named "Corvane Therapeutics" - needs a new PowerPoint design

We need a new PowerPoint Design for an early-stage start-up named "Corvane Therapeutics" seeking to disrupt the current approach towards drug discovery within aging disorders.

We would like to build on Corvane's legacy, the founder of the modern science of genetics, by employing a multidisciplinary approach, experimenting, and providing elderly patients the attention they deserve.

We have selected the suffix "therapeutics" intentionally as it stands for (a medicine) the treatment of disease; the science of healing. Alzheimer’s treatment is a huge, urgent, unmet need:
- Shift from a disease-management system to a preventive medicine system
- Focus on increasing the health span, not only the life span

Target Market(s)

Pharma/ Biotech Executives Medical Institutions Healthcare professionals (MDs, nurses, payors, pharmacists, etc.) Patients

Industry/Entity Type

Healthcare

Other font styles liked:
• Celias

Colors
0054AA
0677BA
7BADD7
CADEEF
E8F1F8
E54698
E96AAD
F1A4CE
F9D9EA
FCEFF6
A7469A
B969AE
D3A5CF
EDDBEB
F8F0F9
6B429C
8869AF
B7A5CE
E3DAEB
F3F0F8

Requirements
Must have
• - differentiate from other companies named after Corvane - differentiate from other Pharma/ Biotech companies
Nice to have
• simplicity/ minimalist logo vivid colors gradient 3D Life-Sciences inspired Simple geometry Balance
Should not have
• mascot/ emblem watermark logo animated ink style nature-inspired inventive typography artistic chaos

```html
<!DOCTYPE html>
<html lang="en">
<head>
<meta charset="utf-8">
<title>Corvane Therapeutics – Presentation Template</title>
<link href="https://fonts.googleapis.com/css2?family=Barlow:ital,wght@0,400;0,500;0,600;0,700;1,400&family=Barlow+Condensed:wght@400;500;700&display=swap" rel="stylesheet">
<style>
  :root{
    --bg:#2b2b2d;
    --white:#ffffff;
    --ink:#1d1d1f;
    --grey-text:#6b6b70;
    --magenta:#b3199c;
    --purple:#6b429c;
    --violet:#7b2fb0;
    --blue:#0677ba;
    --orange:#f7a21b;
    --pink:#ee4f8f;
    --orchid:#b969ae;
  }
  *{margin:0;padding:0;box-sizing:border-box}
  html,body{width:1200px;height:546px;overflow:hidden;background:var(--bg)}
  body{position:relative;font-family:"Barlow",Arial,sans-serif;color:var(--ink)}
  .slide{position:absolute;width:336px;height:189px;overflow:hidden;background:var(--white)}
  .slide > svg.art{position:absolute;inset:0;width:100%;height:100%}
  .abs{position:absolute}
  .col-1{left:73px}.col-2{left:432px}.col-3{left:792px}
  .row-1{top:59px}.row-2{top:275px}

  .brand{position:absolute;font-family:"Barlow",Arial,sans-serif;font-weight:600;line-height:.9}
  .brand .name{display:block}
  .brand .suffix{display:block;letter-spacing:.08em}

  .slide-title{position:absolute;color:var(--magenta);font-weight:700;font-size:14px;line-height:1;letter-spacing:.01em;white-space:nowrap}
  .slide-title em{font-style:italic;font-weight:400;font-size:8px;color:var(--purple);letter-spacing:0}
  .slide-subtitle{position:absolute;font-style:italic;font-size:7.5px;color:var(--ink)}
  .slide-number{position:absolute;font-family:"Barlow Condensed",Arial,sans-serif;font-weight:500;font-size:42px;line-height:1;letter-spacing:-1px}
  .fine{font-size:2.9px;line-height:1.45;color:var(--grey-text);text-align:justify}
  .lead{font-size:5.4px;color:var(--ink)}

  .cover-brand{left:229px;top:79px;color:var(--white)}
  .cover-brand .name{font-size:22px}
  .cover-brand .suffix{font-size:9.5px;margin-top:2px}
  .cover-title{left:164px;top:138px;color:var(--white);font-family:"Barlow Condensed",Arial,sans-serif;font-size:16px;line-height:1;border-bottom:.6px solid var(--white);padding-bottom:1px;white-space:nowrap}
  .cover-title b{font-weight:700}
  .cover-title span{font-weight:400}
  .cover-web{left:203px;top:159px;color:var(--white);font-size:5px;letter-spacing:.28em}

  .member{position:absolute;left:208px;width:110px}
  .member h3{font-weight:500;font-size:7.5px;color:var(--ink)}
  .member p{font-size:4.4px;line-height:1.75;color:var(--grey-text);margin-top:2px}
  .member .phone{font-size:4.4px;color:var(--grey-text);margin-top:2px}
  .member .links{display:flex;gap:5px;margin-top:4px;align-items:center}
  .member .links i{display:block;width:4px;height:4px;border-radius:50%;background:var(--grey-text)}

  .bar-value{position:absolute;font-size:9px;font-weight:400;text-align:center;width:40px}
  .month{position:absolute;top:162px;width:27px;height:4.5px;font-size:3.3px;color:var(--white);text-align:center;line-height:4.5px}
  .month-note{position:absolute;top:169px;width:28px;font-size:2.3px;line-height:1.35;color:#9a9aa0;text-align:center}

  .stat{position:absolute;top:83px;width:56px;text-align:center}
  .stat h4{font-size:3.8px;font-weight:500;color:var(--ink);margin-bottom:3px}
  .stat p{font-size:2.5px;line-height:1.5;color:var(--grey-text)}
  .donut-label{font-family:"Barlow",Arial,sans-serif;font-size:5px;fill:#777}

  .closing-brand{left:17px;top:23px;color:var(--white)}
  .closing-brand .name{font-size:27px}
  .closing-brand .suffix{font-size:11px;margin-top:2px}
  .closing-phone{left:17px;top:145px;color:var(--white);font-size:11px}
  .closing-web{left:17px;top:164px;color:var(--white);font-size:7.8px}
</style>
</head>
<body>

<!-- Slide 1: cover -->
<section class="slide col-1 row-1" aria-label="Cover slide">
  <svg class="art" viewBox="0 0 336 189" preserveAspectRatio="none">
    <defs>
      <linearGradient id="coverBg" x1="0" y1="0" x2="1" y2="1"><stop offset="0" stop-color="#c2189a"/><stop offset="1" stop-color="#7b2fb0"/></linearGradient>
      <linearGradient id="coverPhoto" x1="0" y1="0" x2="1" y2="0"><stop offset="0" stop-color="#c2189a" stop-opacity="0"/><stop offset=".6" stop-color="#d14bb0" stop-opacity=".4"/><stop offset="1" stop-color="#8a3bc0" stop-opacity=".3"/></linearGradient>
      <linearGradient id="coverDeco" x1="0" y1="0" x2="1" y2="0"><stop offset="0" stop-color="#2a4fc0"/><stop offset=".55" stop-color="#1f8fe0" stop-opacity=".75"/><stop offset="1" stop-color="#c2189a" stop-opacity="0"/></linearGradient>
    </defs>
    <rect width="336" height="189" fill="url(#coverBg)"/>
    <rect x="140" width="196" height="189" fill="url(#coverPhoto)" role="img" aria-label="Tinted photo of a scientist working with a microscope in a laboratory"/>
    <rect width="200" height="189" fill="url(#coverDeco)" role="img" aria-label="Decorative blue ribbon artwork"/>
  </svg>
  <div class="brand cover-brand"><span class="name">Corvane</span><span class="suffix">Therapeutics</span></div>
  <div class="abs cover-title"><span>BUSINESS </span><b>PRESENTATION</b></div>
  <div class="abs cover-web">WWW.CORVANEHEALTH.COM</div>
</section>

<!-- Slide 2: text slide -->
<section class="slide col-2 row-1" aria-label="Text slide">
  <svg class="art" viewBox="0 0 336 189" preserveAspectRatio="none">
    <defs>
      <linearGradient id="textWash" x1="0" y1="0" x2="1" y2="0"><stop offset="0" stop-color="#f4f4f6" stop-opacity="0"/><stop offset="1" stop-color="#e6e6ea"/></linearGradient>
      <linearGradient id="textPanel" x1="0" y1="0" x2="1" y2="1"><stop offset="0" stop-color="#c2189a"/><stop offset="1" stop-color="#8d2cae"/></linearGradient>
    </defs>
    <rect x="150" width="140" height="189" fill="url(#textWash)" role="img" aria-label="Faint illustration of neurons and branching nerve cells"/>
    <polygon points="215,0 336,0 336,189 285,189" fill="url(#textPanel)" role="img" aria-label="Decorative magenta ribbon artwork"/>
  </svg>
  <h2 class="slide-title" style="left:9px;top:12px">LOREM IPSUM</h2>
  <div class="slide-subtitle" style="left:9px;top:27px">DOLOR SIT AMET</div>
  <p class="abs lead" style="left:9px;top:44px;width:150px">Lorem ipsum dolor sit amet, consectetur adipiscing elit.</p>
  <p class="abs fine" style="left:9px;top:53px;width:144px">Lorem ipsum dolor sit amet, consectetur adipiscing elit. Mauris consectetur, quam at sagittis malesuada, ex justo luctus arcu, vitae tempor risus odio eu ipsum. Phasellus mauris tortor, lobortis sit amet ex eu, dictum venenatis libero.</p>
  <p class="abs fine" style="left:9px;top:78px;width:144px">Nulla porta, arcu id euismod dictum, nunc elit molestie orci, eget molestie lacus urna id mi. Cras mollis, tellus eget ultricies volutpat, est augue sagittis ipsum, eget posuere nunc augue eget purus. Etiam interdum est nec interdum lobortis. Maecenas mauris augue, bibendum id lacus accumsan, aliquam interdum metus. Sed lobortis lorem vel magna blandit, eget consectetur lectus porttitor.</p>
  <p class="abs fine" style="left:9px;top:127px;width:144px">Quisque dictum neque vitae urna suscipit, cursus euismod libero venenatis. Class aptent taciti sociosqu ad litora torquent per conubia nostra, per inceptos himenaeos.</p>
  <div class="slide-number" style="left:8px;top:151px;color:var(--magenta)">02</div>
  <div class="abs" style="right:8px;top:8px;color:var(--white);font-size:10px;line-height:1;white-space:nowrap"><span style="font-weight:400">TITLE </span><b style="font-size:15px">SLIDE</b></div>
  <div class="brand" style="left:279px;top:170px;color:var(--blue)"><span class="name" style="font-size:11px">Corvane</span><span class="suffix" style="font-size:4.6px;color:var(--ink)">Therapeutics</span></div>
</section>

<!-- Slide 3: team -->
<section class="slide col-3 row-1" aria-label="Team slide">
  <svg class="art" viewBox="0 0 336 189" preserveAspectRatio="none">
    <defs>
      <linearGradient id="teamPanel" x1="0" y1="0" x2="1" y2="1"><stop offset="0" stop-color="#c2189a"/><stop offset="1" stop-color="#6b429c"/></linearGradient>
      <linearGradient id="avatar" x1="0" y1="0" x2="1" y2="1"><stop offset="0" stop-color="#1fa6e8"/><stop offset="1" stop-color="#243a9c"/></linearGradient>
    </defs>
    <polygon points="0,0 70,0 150,189 0,189" fill="url(#teamPanel)" role="img" aria-label="Decorative magenta ribbon artwork"/>
    <polygon points="154,45 166,35 188,35 200,45 200,69 188,79 166,79 154,69" fill="url(#avatar)" role="img" aria-label="Portrait photo of a team member"/>
    <polygon points="154,120 166,110 188,110 200,120 200,144 188,154 166,154 154,144" fill="url(#avatar)" role="img" aria-label="Portrait photo of a team member"/>
  </svg>
  <div class="slide-number" style="left:7px;top:148px;color:var(--white)">03</div>
  <div class="member" style="top:30px">
    <h3>Rena Adler</h3>
    <p>Lorem ipsum dolor sit<br>amet, consectetur<br>adipiscing elit.</p>
    <div class="phone">+123 456 789</div>
    <div class="links">
      <svg width="5" height="4" viewBox="0 0 5 4"><rect x=".25" y=".25" width="4.5" height="3.5" fill="none" stroke="#6b6b70" stroke-width=".5"/><polyline points=".3,.3 2.5,2 4.7,.3" fill="none" stroke="#6b6b70" stroke-width=".5"/></svg>
      <i></i><i></i><i></i>
    </div>
  </div>
  <div class="member" style="top:105px">
    <h3>Rena Adler</h3>
    <p>Lorem ipsum dolor sit<br>amet, consectetur<br>adipiscing elit.</p>
    <div class="phone">+123 456 789</div>
    <div class="links">
      <svg width="5" height="4" viewBox="0 0 5 4"><rect x=".25" y=".25" width="4.5" height="3.5" fill="none" stroke="#6b6b70" stroke-width=".5"/><polyline points=".3,.3 2.5,2 4.7,.3" fill="none" stroke="#6b6b70" stroke-width=".5"/></svg>
      <i></i><i></i><i></i>
    </div>
  </div>
  <div class="brand" style="left:288px;top:168px;color:var(--blue)"><span class="name" style="font-size:11px">Corvane</span><span class="suffix" style="font-size:4.6px;color:var(--ink)">Therapeutics</span></div>
</section>

<!-- Slide 4: growth chart -->
<section class="slide col-1 row-2" aria-label="Chart slide">
  <svg class="art" viewBox="0 0 336 189" preserveAspectRatio="none">
    <defs>
      <linearGradient id="sidePanel" x1="0" y1="0" x2="1" y2="1"><stop offset="0" stop-color="#2a6fd0"/><stop offset=".5" stop-color="#b3199c"/><stop offset="1" stop-color="#3cc3f2"/></linearGradient>
      <linearGradient id="bar1" x1="0" y1="0" x2="0" y2="1"><stop offset="0" stop-color="#fbc531"/><stop offset="1" stop-color="#f7941d"/></linearGradient>
      <linearGradient id="bar2" x1="0" y1="0" x2="0" y2="1"><stop offset="0" stop-color="#f26aa5"/><stop offset="1" stop-color="#e63b7a"/></linearGradient>
      <linearGradient id="bar3" x1="0" y1="0" x2="0" y2="1"><stop offset="0" stop-color="#d35fb0"/><stop offset="1" stop-color="#a24aa8"/></linearGradient>
      <linearGradient id="bar4" x1="0" y1="0" x2="0" y2="1"><stop offset="0" stop-color="#8a4cb8"/><stop offset="1" stop-color="#5d3f9e"/></linearGradient>
      <linearGradient id="bar5" x1="0" y1="0" x2="0" y2="1"><stop offset="0" stop-color="#8c3fb5"/><stop offset="1" stop-color="#6b2fa0"/></linearGradient>
    </defs>
    <g stroke="#ececef" stroke-width=".4">
      <line x1="9" y1="30" x2="190" y2="30"/><line x1="9" y1="40" x2="190" y2="40"/><line x1="9" y1="50" x2="190" y2="50"/>
      <line x1="9" y1="60" x2="190" y2="60"/><line x1="9" y1="70" x2="190" y2="70"/><line x1="9" y1="80" x2="190" y2="80"/>
      <line x1="9" y1="90" x2="190" y2="90"/><line x1="9" y1="100" x2="190" y2="100"/><line x1="9" y1="110" x2="190" y2="110"/>
      <line x1="9" y1="120" x2="190" y2="120"/><line x1="9" y1="130" x2="190" y2="130"/><line x1="9" y1="140" x2="190" y2="140"/><line x1="9" y1="150" x2="190" y2="150"/>
    </g>
    <polygon points="19,157 19,137 32.5,130 46,137 46,157" fill="url(#bar1)"/>
    <polygon points="52,157 52,116 65.5,109 79,116 79,157" fill="url(#bar2)"/>
    <polygon points="85,157 85,104 98.5,97 112,104 112,157" fill="url(#bar3)"/>
    <polygon points="118,157 118,89 131.5,82 145,89 145,157" fill="url(#bar4)"/>
    <polygon points="151,157 151,69 164.5,62 178,69 178,157" fill="url(#bar5)"/>
    <line x1="9" y1="158" x2="190" y2="158" stroke="#555" stroke-width=".8"/>
    <path d="M20,105 C28,96 40,92 66,85 C80,82 90,80 99,77 C115,70 122,60 133,53 C145,45 155,36 166,30" fill="none" stroke="#c9c9cf" stroke-width=".7"/>
    <circle cx="33" cy="96" r="2.2" fill="#f7a21b"/><circle cx="66" cy="85" r="2.2" fill="#ee4f8f"/>
    <circle cx="99" cy="77" r="2.2" fill="#c25fb0"/><circle cx="133" cy="53" r="2.2" fill="#7e4cb6"/><circle cx="166" cy="30" r="2.2" fill="#6b2fa0"/>
    <rect x="237" width="99" height="189" fill="url(#sidePanel)" role="img" aria-label="Decorative blue and magenta ribbon artwork"/>
  </svg>
  <h2 class="slide-title" style="left:11px;top:9px">LOREM IPSUM <em>DOLOR SIT AMET</em></h2>
  <div class="bar-value" style="left:12.5px;top:117px;color:var(--orange)">+12.2</div>
  <div class="bar-value" style="left:45.5px;top:96px;color:var(--pink)">+23.5</div>
  <div class="bar-value" style="left:78.5px;top:84px;color:var(--orchid)">+32.5</div>
  <div class="bar-value" style="left:111.5px;top:68px;color:var(--purple)">+43.3</div>
  <div class="bar-value" style="left:144.5px;top:47px;color:var(--violet)">+55.5</div>
  <div class="month" style="left:19px;background:var(--orange)">January</div>
  <div class="month" style="left:52px;background:var(--pink)">February</div>
  <div class="month" style="left:85px;background:var(--orchid)">March</div>
  <div class="month" style="left:118px;background:#7e4cb6">April</div>
  <div class="month" style="left:151px;background:var(--violet)">June</div>
  <p class="month-note" style="left:18.5px">Lorem ipsum dolor sit amet, consectetur adip.</p>
  <p class="month-note" style="left:51.5px">Lorem ipsum dolor sit amet, consectetur adip.</p>
  <p class="month-note" style="left:84.5px">Lorem ipsum dolor sit amet, consectetur adip.</p>
  <p class="month-note" style="left:117.5px">Lorem ipsum dolor sit amet, consectetur adip.</p>
  <p class="month-note" style="left:150.5px">Lorem ipsum dolor sit amet, consectetur adip.</p>
  <div class="slide-number" style="left:196px;top:146px;color:var(--blue)">04</div>
</section>

<!-- Slide 5: key figures -->
<section class="slide col-2 row-2" aria-label="Figures slide">
  <svg class="art" viewBox="0 0 336 189" preserveAspectRatio="none">
    <defs>
      <linearGradient id="leftPanel" x1="0" y1="0" x2="1" y2="1"><stop offset="0" stop-color="#3cc3f2"/><stop offset=".5" stop-color="#b3199c"/><stop offset="1" stop-color="#243a9c"/></linearGradient>
    </defs>
    <rect width="100" height="189" fill="url(#leftPanel)" role="img" aria-label="Decorative blue and magenta ribbon artwork"/>
    <line x1="108" y1="24" x2="330" y2="24" stroke="#6b429c" stroke-width=".6"/>
    <g fill="none" stroke-width="6">
      <circle cx="142" cy="54" r="16" stroke="#eee"/>
      <circle cx="142" cy="54" r="16" stroke="#b3199c" stroke-dasharray="90.5 100.5" transform="rotate(-90 142 54)"/>
      <circle cx="215" cy="54" r="16" stroke="#eee"/>
      <circle cx="215" cy="54" r="16" stroke="#c540a6" stroke-dasharray="75.4 100.5" transform="rotate(-90 215 54)"/>
      <circle cx="284" cy="54" r="16" stroke="#eee"/>
      <circle cx="284" cy="54" r="16" stroke="#cf6fb8" stroke-dasharray="60.3 100.5" transform="rotate(-90 284 54)"/>
    </g>
    <text class="donut-label" x="142" y="56" text-anchor="middle">90%</text>
    <text class="donut-label" x="215" y="56" text-anchor="middle">75%</text>
    <text class="donut-label" x="284" y="56" text-anchor="middle">60%</text>
  </svg>
  <h2 class="slide-title" style="left:107px;top:9px">LOREM IPSUM <em>DOLOR SIT AMET</em></h2>
  <div class="stat" style="left:114px"><h4>Lorem ipsum dolor</h4><p>Lorem ipsum dolor sit amet, consectetur adipiscing elit. Mauris consectetur, quam at sagittis malesuada, ex justo luctus arcu. Phasellus mauris tortor, lobortis sit amet ex eu, dictum venenatis libero. Nulla porta, arcu id euismod dictum, nunc elit molestie orci.</p></div>
  <div class="stat" style="left:187px"><h4>Lorem ipsum dolor</h4><p>Lorem ipsum dolor sit amet, consectetur adipiscing elit. Mauris consectetur, quam at sagittis malesuada, ex justo luctus arcu. Phasellus mauris tortor, lobortis sit amet ex eu, dictum venenatis libero. Nulla porta, arcu id euismod dictum, nunc elit molestie orci.</p></div>
  <div class="stat" style="left:256px"><h4>Lorem ipsum dolor</h4><p>Lorem ipsum dolor sit amet, consectetur adipiscing elit. Mauris consectetur, quam at sagittis malesuada, ex justo luctus arcu. Phasellus mauris tortor, lobortis sit amet ex eu, dictum venenatis libero. Nulla porta, arcu id euismod dictum, nunc elit molestie orci.</p></div>
  <div class="brand" style="left:107px;top:167px;color:var(--blue)"><span class="name" style="font-size:11px">Corvane</span><span class="suffix" style="font-size:4.6px;color:var(--ink)">Therapeutics</span></div>
  <div class="slide-number" style="left:289px;top:146px;color:var(--blue)">05</div>
</section>

<!-- Slide 6: closing -->
<section class="slide col-3 row-2" aria-label="Closing slide">
  <svg class="art" viewBox="0 0 336 189" preserveAspectRatio="none">
    <defs>
      <linearGradient id="closeBg" x1="0" y1="0" x2="1" y2="1"><stop offset="0" stop-color="#1c8fe0"/><stop offset="1" stop-color="#1aa9ec"/></linearGradient>
      <radialGradient id="closeCells" cx=".45" cy=".5" r=".6"><stop offset="0" stop-color="#7fd3f7" stop-opacity=".35"/><stop offset="1" stop-color="#1c8fe0" stop-opacity="0"/></radialGradient>
      <linearGradient id="closeDeco" x1="0" y1="0" x2="1" y2="0"><stop offset="0" stop-color="#1c8fe0" stop-opacity="0"/><stop offset=".45" stop-color="#b3199c" stop-opacity=".85"/><stop offset="1" stop-color="#243a9c"/></linearGradient>
    </defs>
    <rect width="336" height="189" fill="url(#closeBg)"/>
    <rect width="336" height="189" fill="url(#closeCells)" role="img" aria-label="Faint microscope image of cells in blue"/>
    <rect x="160" width="176" height="189" fill="url(#closeDeco)" role="img" aria-label="Decorative magenta and blue ribbon artwork"/>
  </svg>
  <div class="brand closing-brand"><span class="name">Corvane</span><span class="suffix">Therapeutics</span></div>
  <div class="abs closing-phone">+123 456 789</div>
  <div class="abs closing-web">WWW.CORVANEHEALTH.COM</div>
</section>

</body>
</html>
```